Branding Guide and Website for Q7Systems

Need an experienced Graphics Designer with a proven track record to create a design and branding guide for all media formats. From this guide you will then create a new website design for Q7systems.com.
There will be 8 pages (to start) with the new website. Each page will have multiple features and panels each need to have individual attention and customization that collectively fit together into a single cohesive look and feel.
We have not been able to get good designs I’m attaching one version which is the best we’ve received which is not bad but needs to be polished up better and the images need to change. I’d like to have some other accent colors but not too much I like the white, dark blue, gray, dark gray style.
Here are some sites that I like –
http://www.brelvant.com/
https://www.vontaric.com/ (layout good, graphics not great)
http://www.glastrek.com/ (good layout and graphics, too much animation)
https://www.pendrowix.com/ (a little boring but the colors and some of the top images are good)
https://www.tarnowelk.com/ (a little over the top colors are off but they have some good info graphics)
We don’t expect you will code the site however if you have that capability we’ll need it responsive/flat for mobile. Otherwise we can find someone to do the programming and we’ll just need the design files and images.
Branding guide will be used for web, email, print etc. so you’ll need to consider all guidelines for all formats. That is about it let me know if any questions we can have a call to discuss further if it is easier.
Not sure why they want a minimum of 300 words I’m done now but apparently have to keep typing so that is what I’m doing and Ok I’m at 300 words, almost there and we’re here now.

Target Market(s)

Customers looking for IT Services, Private Cloud, Security Services, Advanced Support, Fully Managed or Co-Managed IT.

Industry/Entity Type

It Company

Number of Pages Required

5+ page

Font styles to use
Sans Serif

Colors
0255a3
959595
e6e6e6
ffffff

Requirements
Must have
• Clean, professional and modern look using iconography, info graphics, flat etc.

```html
<!DOCTYPE html>
<html lang="en">
<head>
<meta charset="utf-8">
<title>Q7Systems — IT Service Excellence</title>
<link href="https://fonts.googleapis.com/css2?family=Open+Sans:wght@400;600;700;800&display=swap" rel="stylesheet">
<style>
:root{
  --blue:#0255a3;
  --blue-dark:#013a72;
  --gray:#959595;
  --gray-dark:#3a3a3a;
  --light:#e6e6e6;
  --white:#ffffff;
  --orange:#f39c12;
  --footer:#262626;
  --text:#555;
}
*{box-sizing:border-box;margin:0;padding:0}
html,body{width:1200px;height:2704px;overflow:hidden}
body{font-family:"Open Sans",Arial,sans-serif;color:var(--text);background:var(--white);font-size:13px;line-height:1.6}
.site-header{height:64px;display:flex;align-items:center;justify-content:space-between;padding:0 60px;background:var(--white);border-bottom:1px solid var(--light)}
.brand{display:flex;align-items:center;gap:10px;font-weight:800;font-size:22px;color:var(--blue)}
.brand-mark{width:18px;height:18px;background:var(--blue);border-radius:50%}
.main-nav{display:flex;gap:26px;font-size:11px;font-weight:600;color:var(--gray-dark)}
.main-nav a{color:inherit;text-decoration:none;padding:22px 0}
.main-nav a.active{color:var(--white);background:var(--blue);padding:22px 14px}
.hero{position:relative;height:336px;background:linear-gradient(115deg,#02284f 0%,#0451a0 45%,#2a86d8 70%,#0b3f7a 100%);color:var(--white);overflow:hidden}
.hero-visual{position:absolute;right:0;top:0;width:640px;height:336px;background:radial-gradient(circle at 55% 45%,rgba(170,220,255,.55),rgba(30,110,200,.15) 45%,transparent 70%)}
.hero-copy{position:absolute;left:120px;top:108px}
.hero h1{font-size:38px;font-weight:800;letter-spacing:.5px;line-height:1.1}
.hero p{font-size:15px;margin-top:8px}
.btn-orange{display:inline-block;margin-top:22px;background:var(--orange);color:var(--white);font-weight:700;font-size:12px;padding:12px 22px;border-radius:2px}
.hero-arrow{position:absolute;top:150px;width:30px;height:40px;background:rgba(0,0,0,.3);display:flex;align-items:center;justify-content:center}
.hero-arrow.left{left:0}.hero-arrow.right{right:0}
.section-title{text-align:center;font-size:25px;font-weight:800;color:var(--gray-dark);letter-spacing:.5px}
.title-rule{width:50px;height:3px;background:var(--blue);margin:10px auto 16px}
.section-intro{text-align:center;max-width:560px;margin:0 auto;font-size:13px;color:var(--text)}
.what-we-do{height:520px;padding-top:50px}
.services{display:grid;grid-template-columns:repeat(3,300px);column-gap:40px;row-gap:48px;justify-content:center;margin-top:52px}
.service{display:flex;gap:16px}
.service svg{flex:none}
.service h3{font-size:17px;font-weight:600;color:var(--gray-dark);margin-bottom:6px}
.service p{font-size:12px;color:var(--gray);line-height:1.55}
.help{height:770px;padding-top:50px;border-top:1px solid var(--light)}
.help-grid{display:grid;grid-template-columns:repeat(4,220px);gap:28px;justify-content:center;margin-top:40px}
.help-photo{height:170px}
.help-card{text-align:center}
.help-card h3{font-size:17px;font-weight:600;color:var(--gray-dark);margin:14px 0 4px}
.help-card p{font-size:12px;color:var(--gray)}
.partners-intro{text-align:center;font-size:12px;margin-top:46px;color:var(--text)}
.partners{display:flex;justify-content:center;gap:64px;margin-top:26px;font-size:24px;font-weight:600;color:var(--gray)}
.partners span{display:flex;align-items:center;gap:8px}
.partners i{width:16px;height:16px;background:var(--gray);border-radius:50%}
.testimonials{height:350px;background:#f2f2f2;padding-top:50px}
.quotes{display:grid;grid-template-columns:repeat(3,300px);gap:50px;justify-content:center;margin-top:34px}
.quote{text-align:center;font-size:12px;color:var(--text);font-style:italic}
.quote cite{display:block;margin-top:16px;color:var(--blue);font-weight:600}
.different{position:relative;height:350px;padding-top:54px}
.different .section-intro{max-width:640px}
.btn-blue{display:block;width:140px;margin:28px auto 0;background:var(--blue);color:var(--white);text-align:center;font-weight:700;font-size:12px;padding:12px 0;border-radius:2px}
.character{position:absolute;right:0;top:20px;width:210px;height:320px;background:linear-gradient(180deg,#f1f4f8,#d9e3ee);border-radius:6px}
.site-footer{height:314px;background:var(--footer);color:#bbb;display:grid;grid-template-columns:200px 230px 230px 230px;gap:40px;padding:40px 60px 0;font-size:12px;position:relative}
.socials{display:flex;gap:8px;margin-bottom:16px}
.socials span{width:26px;height:26px;border:1.5px solid #bbb;border-radius:50%}
.site-footer h4{color:var(--white);font-size:15px;font-weight:600;margin-bottom:12px}
.field{height:28px;background:var(--white);margin-bottom:8px;padding:5px 10px;color:var(--gray)}
.btn-subscribe{width:80px;background:var(--blue);color:var(--white);text-align:center;font-weight:700;padding:6px 0}
.browse li{list-style:none;padding-left:12px;position:relative;margin-bottom:4px}
.browse li::before{content:"";position:absolute;left:0;top:8px;width:5px;height:5px;background:var(--blue)}
.to-top{position:absolute;right:30px;bottom:20px;color:#bbb;font-size:11px}
</style>
</head>
<body>
<header class="site-header">
  <div class="brand"><span class="brand-mark"></span>Q7Systems</div>
  <nav class="main-nav">
    <a class="active">HOME</a><a>MANAGED SERVICES</a><a>PRIVATE CLOUD</a><a>CLOUD SOLUTIONS</a><a>SECURITY SERVICES</a><a>SUPPORT</a><a>COMPANY</a>
  </nav>
</header>

<section class="hero">
  <div class="hero-visual" role="img" aria-label="Glowing blue globe connected to cloud and network devices"></div>
  <div class="hero-copy">
    <h1>IT SERVICE EXCELLENCE</h1>
    <p>Striving for Continuous Serviceimprovement for our Clients</p>
    <span class="btn-orange">GET STARTED NOW</span>
  </div>
  <div class="hero-arrow left"><svg width="10" height="16"><path d="M8 1 2 8l6 7" stroke="#fff" stroke-width="2" fill="none"/></svg></div>
  <div class="hero-arrow right"><svg width="10" height="16"><path d="M2 1l6 7-6 7" stroke="#fff" stroke-width="2" fill="none"/></svg></div>
</section>

<section class="what-we-do">
  <h2 class="section-title">WHAT WE DO</h2>
  <div class="title-rule"></div>
  <p class="section-intro">Providing <b style="color:var(--blue)">Q7Systems</b> IT solutions tailored to small and mid-sized businesses across the region with care since 2004.</p>
  <div class="services">
    <div class="service">
      <svg width="40" height="40" viewBox="0 0 40 40"><circle cx="20" cy="20" r="8" fill="none" stroke="#0255a3" stroke-width="3"/><path d="M20 4v6M20 30v6M4 20h6M30 20h6M9 9l4 4M27 27l4 4M31 9l-4 4M13 27l-4 4" stroke="#0255a3" stroke-width="3"/></svg>
      <div><h3>Managed Services</h3><p>We provide comprehensive technology management, IT solutions and support. Whether you engineer or grow.</p></div>
    </div>
    <div class="service">
      <svg width="40" height="40" viewBox="0 0 40 40"><path d="M11 30a8 8 0 0 1 1-16 10 10 0 0 1 19 3 7 7 0 0 1-1 13z" fill="#0255a3"/></svg>
      <div><h3>Private Cloud</h3><p>We put systems and applications into the cloud so your team works from anywhere, safely and fast.</p></div>
    </div>
    <div class="service">
      <svg width="40" height="40" viewBox="0 0 40 40"><path d="M20 4 34 9v10c0 9-6 15-14 17C12 34 6 28 6 19V9z" fill="#0255a3"/><path d="M14 20l4 4 8-8" stroke="#fff" stroke-width="3" fill="none"/></svg>
      <div><h3>Security Services</h3><p>To prevent intrusion and maintain uptime, we guard your network against every kind of modern threat.</p></div>
    </div>
    <div class="service">
      <svg width="40" height="40" viewBox="0 0 40 40"><path d="M7 22a13 13 0 0 1 26 0" stroke="#0255a3" stroke-width="3" fill="none"/><rect x="5" y="21" width="7" height="11" rx="2" fill="#0255a3"/><rect x="28" y="21" width="7" height="11" rx="2" fill="#0255a3"/></svg>
      <div><h3>Advanced Support</h3><p>Talk to certified engineers who know your systems and resolve problems quickly on every single call.</p></div>
    </div>
    <div class="service">
      <svg width="40" height="40" viewBox="0 0 40 40"><rect x="15" y="4" width="10" height="8" fill="#0255a3"/><rect x="4" y="28" width="10" height="8" fill="#0255a3"/><rect x="26" y="28" width="10" height="8" fill="#0255a3"/><path d="M20 12v8M9 28v-8h22v8" stroke="#0255a3" stroke-width="3" fill="none"/></svg>
      <div><h3>Network Services</h3><p>From installation to monitoring, we keep your network reliable, fast and ready for growth today.</p></div>
    </div>
    <div class="service">
      <svg width="40" height="40" viewBox="0 0 40 40"><path d="M32 20a12 12 0 1 1-4-9" stroke="#0255a3" stroke-width="3.5" fill="none"/><path d="M24 6h8v8" stroke="#0255a3" stroke-width="3.5" fill="none"/></svg>
      <div><h3>Disaster Recovery</h3><p>Backup and recovery plans that restore your data and operations in minutes when the unexpected hits.</p></div>
    </div>
  </div>
</section>

<section class="help">
  <h2 class="section-title">HOW CAN WE HELP YOUR BUSINESS?</h2>
  <div class="title-rule"></div>
  <p class="section-intro">Our standard managed service plans let you budget for <b style="color:var(--blue)">complete technology management</b> and stay focused on the work that grows your business every day.</p>
  <div class="help-grid">
    <div class="help-card"><div class="help-photo" role="img" aria-label="Network cables plugged into a switch" style="background:linear-gradient(135deg,#1d2f4a,#5a7fa8)"></div><h3>Your Network</h3><p>Fast, reliable connectivity with proactive monitoring.</p></div>
    <div class="help-card"><div class="help-photo" role="img" aria-label="Padlock over a glowing red web interface" style="background:linear-gradient(135deg,#3a0b12,#b4303f)"></div><h3>Your Web Presence</h3><p>Secure hosting that keeps your website always online.</p></div>
    <div class="help-card"><div class="help-photo" role="img" aria-label="Hands typing on a laptop keyboard" style="background:linear-gradient(135deg,#2b2b2b,#8a8a8a)"></div><h3>Your Applications</h3><p>Business software deployed and supported from the cloud.</p></div>
    <div class="help-card"><div class="help-photo" role="img" aria-label="Technician working between server racks" style="background:linear-gradient(135deg,#2c3440,#a9b4c2)"></div><h3>Your Piece of Mind</h3><p>Clear strategy and trusted advice whenever you need.</p></div>
  </div>
  <p class="partners-intro">We work with leading companies to deliver trusted technology solutions for every <b style="color:var(--blue)">client we serve</b>.</p>
  <div class="partners">
    <span><i></i>Sonvra</span><span><i></i>Mirelta</span><span>Pictavo</span><span>Stillvane</span><span><i style="border-radius:0"></i>Quadrel</span>
  </div>
</section>

<section class="testimonials">
  <h2 class="section-title">WHAT ARE PEOPLE SAYING ABOUT Q7SYSTEMS</h2>
  <div class="title-rule"></div>
  <div class="quotes">
    <div class="quote">“Since moving to their managed plan our downtime has nearly disappeared, and the support team always answers quickly with clear, friendly help for every question our staff brings.”<cite>Dana Orlen, City Name</cite></div>
    <div class="quote">“They moved our whole office into a private cloud over one weekend. Monday morning everything simply worked, and our people could reach their files from anywhere at all.”<cite>Dana Orlen, City Name</cite></div>
    <div class="quote">“Their security review found gaps we never knew existed. Now we sleep better knowing our client data is protected, backed up and watched around the clock every day.”<cite>Dana Orlen, City Name</cite></div>
  </div>
</section>

<section class="different">
  <h2 class="section-title">WE ARE DIFFERENT</h2>
  <div class="title-rule"></div>
  <p class="section-intro">We build long partnerships, not one-off fixes. Our engineers learn how your business works, plan ahead for growth and keep your technology running smoothly, so you can focus on customers while we take care of the systems behind them every single day of the year.</p>
  <span class="btn-blue">HOW IT WORKS</span>
  <div class="character" role="img" aria-label="Cartoon IT consultant with glasses holding a tablet"></div>
</section>

<footer class="site-footer">
  <div>
    <div class="socials"><span></span><span></span><span></span><span></span></div>
    <p>© 2016 Q7Systems Inc.<br>All Rights Reserved<br>Privacy Policy</p>
  </div>
  <div>
    <h4>Contact us</h4>
    <p>1420 Harbor View Drive, Suite 210<br>Northgate, CA 90000<br>+1 555 014 7720<br>hello@q7systems.com</p>
  </div>
  <div>
    <h4>Newsletter</h4>
    <div class="field">Name</div>
    <div class="field">Email address</div>
    <div class="btn-subscribe">SUBMIT</div>
  </div>
  <div>
    <h4>Browse</h4>
    <ul class="browse"><li>Managed Services</li><li>IT Private Cloud</li><li>Security Services</li><li>Network Services</li><li>Disaster Recovery</li></ul>
  </div>
  <span class="to-top">▲ UP</span>
</footer>
</body>
</html>
```